Website for 3d printing & other services

Hi, i'm after a website to sell my 3d printed automotive parts as well as sell my 3d printing services & other services.

There's a few things i need the website to have:

- Automatic 3d print quoting based on the file the client uploads to the website.
- Shop function where i can sell my custom automotive parts
- 3D printing technologies offered are SLA & FDM
- My business can offer 3d printing, 3d scanning, 3d cad design, cnc machining, steel fabrication, drafting services.

The color design is to suit my logo which is Black, orange & white.

Target Market(s)

3d printing, automotive, fabrication

Industry/Entity Type

General manufacturing & Custom automotive parts

Coding

Coded - Design and coding required

Number of Pages Required

5+ page

Requirements
Must have
• Automatic 3d print quoting. Shop for my printed parts.

```html
<!DOCTYPE html>
<html lang="en">
<head>
<meta charset="utf-8">
<title>RNX Draft &amp; Design</title>
<link href="https://fonts.googleapis.com/css2?family=Poppins:wght@400;500;600;700;800;900&display=swap" rel="stylesheet">
<style>
:root{
  --orange:#ff6f00;
  --black:#0c0c0c;
  --ink:#1b1b1b;
  --text:#3a3a3a;
  --grey-bg:#efefef;
  --card-bg:#f4f4f4;
  --white:#ffffff;
  --dark-panel:#15151b;
}
*{box-sizing:border-box;margin:0;padding:0}
html,body{width:1200px;height:3186px;overflow:hidden}
body{font-family:'Poppins',sans-serif;color:var(--text);background:var(--white);position:relative}
a{text-decoration:none}
.abs{position:absolute}
.btn{position:absolute;width:155px;height:42px;background:var(--orange);color:var(--white);font-weight:700;font-size:15px;display:flex;align-items:center;justify-content:center;text-transform:uppercase;letter-spacing:-.2px;text-decoration:none}
.heading{font-weight:800;color:var(--orange);text-transform:uppercase;letter-spacing:-.5px;line-height:1.2}
.brand{color:var(--orange);font-weight:800;text-align:center;line-height:1}
.brand .brand-big{display:block;font-size:44px;letter-spacing:-1px}
.brand .brand-small{display:block;font-size:12.5px;margin-top:4px}

/* hero */
.hero{position:absolute;left:0;top:0;width:1200px;height:596px;background:linear-gradient(90deg,#ffffff 0%,#ffffff 40%,#e6eaef 70%,#d3d9e1 100%)}
.hero-photo{position:absolute;left:640px;top:0;width:560px;height:596px;background:linear-gradient(90deg,rgba(255,255,255,0) 0%,rgba(190,198,208,.55) 35%,rgba(150,158,168,.6) 60%,rgba(200,206,214,.5) 100%)}
.site-logo{left:124px;top:12px;width:124px}
.main-nav{left:0;top:34px;width:1200px;height:20px}
.main-nav a{position:absolute;font-size:14px;font-weight:500;color:var(--ink);white-space:nowrap}
.hero-title{left:110px;top:205px;font-size:54px;line-height:56px}
.hero-copy{left:110px;top:336px;font-size:17.5px;line-height:32px;color:var(--ink)}
.slider-dot{position:absolute;width:30px;height:30px;border-radius:50%;border:1.5px solid #333;display:flex;align-items:center;justify-content:center}

/* automotive */
.parts-photo{left:0;top:599px;width:495px;height:551px;background:linear-gradient(150deg,#c9c9c9 0%,#8e8e8e 35%,#5a5a5a 65%,#9a9a9a 100%)}
.parts-bar{left:495px;top:599px;width:8px;height:551px;background:var(--orange)}
.parts-title{left:605px;top:690px;font-size:36px;line-height:47px}
.parts-copy{left:605px;top:803px;width:482px;font-size:16.3px;line-height:30px;text-align:justify;hyphens:auto;color:var(--text)}

/* services */
.services{left:0;top:1150px;width:1200px;height:567px;background:var(--grey-bg)}
.section-title{left:0;width:1200px;text-align:center;font-size:37px}
.service-card{position:absolute;top:1330px;width:278px;height:231px;border-left:8px solid var(--orange);border-right:6px solid var(--orange)}
.service-label{position:absolute;top:1580px;width:278px;text-align:center;font-size:17px;color:var(--ink)}

/* technologies */
.tech-card{position:absolute;top:1924px;width:475px;height:342px;background:var(--card-bg);box-shadow:0 4px 12px rgba(0,0,0,.08)}
.tech-photo{position:absolute;left:0;top:0;width:223px;height:327px}
.tech-bar{position:absolute;left:223px;top:0;width:6px;height:327px;background:var(--orange)}
.tech-name{position:absolute;left:256px;top:30px;font-size:26px;font-weight:600;color:var(--ink)}
.tech-copy{position:absolute;left:254px;top:76px;width:218px;font-size:15.8px;line-height:30px;color:var(--text)}

/* quote & contact */
.quote{left:0;top:2353px;width:677px;height:480px;background:var(--orange)}
.contact{left:677px;top:2353px;width:523px;height:480px;background:radial-gradient(ellipse at 60% 40%,#2a2a32 0%,var(--dark-panel) 60%,#0a0a0d 100%)}
.white-title{color:var(--white);font-weight:800;text-transform:uppercase;font-size:37px;letter-spacing:-.5px}
.field{position:absolute;width:245px;height:60px;border:1.5px solid rgba(255,255,255,.85);color:var(--white);font-size:15.5px;padding-left:24px;display:flex;align-items:center}
.upload-field{position:absolute;left:111px;top:2681px;width:499px;height:50px;border:1.5px dashed rgba(255,255,255,.9);color:var(--white);font-size:15px;display:flex;align-items:center;gap:12px;padding-left:22px}
.price-estimate{position:absolute;left:290px;top:2758px;color:var(--white);font-size:15.5px;line-height:26px}
.price-estimate strong{font-weight:700}
.contact-line{position:absolute;left:730px;color:var(--white);font-size:19.5px;line-height:29px}

/* footer */
.footer{left:0;top:2833px;width:1200px;height:353px;background:var(--black)}
.footer-nav a{position:absolute;top:3018px;font-size:15.5px;font-weight:500;color:var(--white);white-space:nowrap}
.social a{position:absolute;top:3068px;width:14px;height:14px;border-radius:50%;background:var(--white)}
.footer-rule{left:111px;top:3121px;width:978px;height:1px;background:#777}
.copyright{left:0;top:3140px;width:1200px;text-align:center;color:var(--white);font-size:14px}
</style>
</head>
<body>

<section class="hero">
  <div class="hero-photo" role="img" aria-label="3D printer nozzle printing a pelvis bone model in a bright medical lab"></div>
</section>
<div class="abs brand site-logo"><span class="brand-big">RNX</span><span class="brand-small">DRAFT &amp; DESIGN</span></div>
<nav class="abs main-nav">
  <a href="#" style="left:423px">ABOUT US</a>
  <a href="#" style="left:535px">SERVICES</a>
  <a href="#" style="left:641px">CUSTOM AUTOMOTIVE PARTS</a>
  <a href="#" style="left:885px">3D PRINTING TECHNOLOGIES</a>
</nav>
<h1 class="abs heading hero-title">Welcome to<br>RNX Draft &amp; Design</h1>
<p class="abs hero-copy">Lorem ipsum dolor sit amet, consectetur adipiscing elit,<br>sed eiusmod tempor incididunt ut labore et dolore magna aliqua.</p>
<a class="btn" href="#" style="left:113px;top:426px">Get Started</a>
<div class="slider-dot" style="left:1127px;top:303px;border-color:#fff">
  <svg width="10" height="12" viewBox="0 0 10 12"><path d="M3 1l5 5-5 5" fill="none" stroke="#fff" stroke-width="1.5"/></svg>
</div>

<div class="abs parts-photo" role="img" aria-label="Metal deposition nozzle printing a textured grey automotive part"></div>
<div class="abs parts-bar"></div>
<h2 class="abs heading parts-title">My Custom Automotive<br>Parts</h2>
<p class="abs parts-copy" lang="en">Sed ut perspiciatis unde omnis iste natus error sit voluptatem accusantium doloremque laudantium, totam rem aperiam, eaque ipsa quae ab illo inventore veritatis et quasi architecto beatae vitae dicta sunt explicabo. Nemo enim ipsam vo-luptatem quia voluptas sit aspernatur aut odit aut fugit, sed quia consequuntur magni</p>
<a class="btn" href="#" style="left:607px;top:1009px">Shop Now</a>

<section class="abs services"></section>
<h2 class="abs heading section-title" style="top:1245px">Our Services</h2>
<div class="slider-dot" style="left:43px;top:1422px">
  <svg width="10" height="12" viewBox="0 0 10 12"><path d="M7 1L2 6l5 5" fill="none" stroke="#333" stroke-width="1.5"/></svg>
</div>
<div class="slider-dot" style="left:1127px;top:1421px">
  <svg width="10" height="12" viewBox="0 0 10 12"><path d="M3 1l5 5-5 5" fill="none" stroke="#333" stroke-width="1.5"/></svg>
</div>
<div class="service-card" style="left:152px;background:linear-gradient(135deg,#1d3d8a 0%,#0e1630 55%,#c83a2a 100%)" role="img" aria-label="3D printer bed with a printed gear"></div>
<div class="service-card" style="left:454px;background:linear-gradient(120deg,#d9d4d2 0%,#e58a80 40%,#c9c9c9 70%,#3a3a3a 100%)" role="img" aria-label="Handheld scanner scanning an engine block"></div>
<div class="service-card" style="left:751px;background:linear-gradient(135deg,#0a2a4a 0%,#1e5f95 50%,#0b1a30 100%)" role="img" aria-label="Holographic car model in a CAD design session"></div>
<div class="service-label" style="left:152px">3D PRINTING</div>
<div class="service-label" style="left:454px">3D SCANNING</div>
<div class="service-label" style="left:751px">3D CAD DESIGN</div>

<h2 class="abs heading section-title" style="top:1800px">3D Printing Technologies</h2>
<article class="tech-card" style="left:111px">
  <div class="tech-photo" role="img" aria-label="Resin printer nozzle forming an ornate heart-shaped print" style="background:linear-gradient(160deg,#2a2622 0%,#8a6a45 45%,#d9b88a 70%,#4a3a2a 100%)"></div>
  <div class="tech-bar"></div>
  <h3 class="tech-name">SLA</h3>
  <p class="tech-copy">Sed ut perspiciatis unde omnis iste natus error sit voluptatem accusantium doloremque laudantium, totam rem aperiam, eaque ipsa quae ab illo inventore veritatis et</p>
</article>
<a class="btn" href="#" style="left:362px;top:2224px">Read More</a>
<article class="tech-card" style="left:610px">
  <div class="tech-photo" role="img" aria-label="Filament printer extruder printing a black twisted vase" style="background:linear-gradient(180deg,#e8e8e8 0%,#9a9a9a 35%,#2a2a2a 70%,#d0d0d0 100%)"></div>
  <div class="tech-bar"></div>
  <h3 class="tech-name">FDM</h3>
  <p class="tech-copy">Sed ut perspiciatis unde omnis iste natus error sit voluptatem accusantium doloremque laudantium, totam rem aperiam, eaque ipsa quae ab illo inventore veritatis et</p>
</article>
<a class="btn" href="#" style="left:861px;top:2224px">Read More</a>

<section class="abs quote"></section>
<section class="abs contact" role="img" aria-label="Dark workshop background behind contact details"></section>
<h2 class="abs white-title" style="left:114px;top:2437px">Get a Quote</h2>
<div class="field" style="left:111px;top:2543px">First Name</div>
<div class="field" style="left:365px;top:2543px">Last Name</div>
<div class="field" style="left:111px;top:2612px">Email</div>
<div class="field" style="left:365px;top:2612px">Phone</div>
<label class="upload-field">
  <svg width="18" height="18" viewBox="0 0 18 18" aria-hidden="true"><path d="M9 13V3M5 7l4-4 4 4M3 15h12" fill="none" stroke="#fff" stroke-width="1.8"/></svg>
  Upload your 3D file (STL, OBJ, STEP) for an instant quote
</label>
<p class="price-estimate">Instant estimate: <strong>$0.00</strong> &middot; updates on upload</p>
<a class="btn" href="#" style="left:111px;top:2750px;background:var(--white);color:var(--orange)">Submit</a>
<h2 class="abs white-title" style="left:717px;top:2435px">Contact Us</h2>
<p class="contact-line" style="top:2525px">Lorem ipsum dolor sit amet,<br>consectetur adipiscing elit, sed</p>
<p class="contact-line" style="top:2603px">+1 555 010 0188</p>
<p class="contact-line" style="top:2653px;left:733px">hello@rnxdraft.test</p>

<footer class="abs footer"></footer>
<div class="abs brand" style="left:540px;top:2895px;width:120px"><span class="brand-big">RNX</span><span class="brand-small">DRAFT &amp; DESIGN</span></div>
<nav class="footer-nav">
  <a href="#" style="left:228px">ABOUT US</a>
  <a href="#" style="left:353px">SERVICES</a>
  <a href="#" style="left:473px">CUSTOM AUTOMOTIVE PARTS</a>
  <a href="#" style="left:747px">3D PRINTING TECHNOLOGIES</a>
</nav>
<div class="social">
  <a href="#" style="left:509px" aria-label="Social profile 1"></a>
  <a href="#" style="left:546px" aria-label="Social profile 2"></a>
  <a href="#" style="left:581px" aria-label="Social profile 3"></a>
  <a href="#" style="left:628px" aria-label="Social profile 4"></a>
  <a href="#" style="left:679px" aria-label="Social profile 5"></a>
</div>
<div class="abs footer-rule"></div>
<p class="abs copyright">© 2023 &nbsp;All Rights Reserved.</p>

</body>
</html>
```